New Dental Office Needs an Attractive and user friendly Website Designed

I need a website for a new dental office. The Name is Harrowfield Dentistry. I would like a Modern design with a user friendly interface and usability.
I would like a landing page, a page that lists the services we offer: Cosmetic Dentistry, Implants, Dental Hygiene, Emergency Services, Restorations, Dentures
Target Market(s)
Mid to upper class
Industry/Entity Type
Dentistry
Coding
Number of Pages Required
1 page
Requirements
Must have
- Landing page that has a scheduling option, Procedures, operating hours, and contact us info
Nice to have
- Appealing design, Soft comforting colors. Easy to navigate page, Modern and professional.

```html
<!DOCTYPE html>
<html lang="en">
<head>
<meta charset="utf-8">
<title>Harrowfield Dentistry</title>
<link href="https://fonts.googleapis.com/css2?family=Figtree:wght@400;500;600;700;800&family=Arimo:wght@400;700&display=swap" rel="stylesheet">
<style>
:root{
  --blue:#0a9ad6;
  --blue-bright:#14aee6;
  --blue-deep:#0b7fc0;
  --ink:#1d1d1f;
  --text:#3a3a3a;
  --pale:#e6f6fd;
  --white:#ffffff;
}
*{box-sizing:border-box;margin:0;padding:0}
html,body{width:1200px;height:3238px;overflow:hidden;background:var(--white)}
body{font-family:"Arimo",Arial,sans-serif;color:var(--text);position:relative}
.abs{position:absolute}
h1,h2,h3,.head{font-family:"Figtree",Arial,sans-serif}
.btn{display:inline-flex;align-items:center;gap:10px;border-radius:30px;font-family:"Figtree",Arial,sans-serif;font-weight:700;text-decoration:none}
.arrow{width:17px;height:17px;border-radius:50%;background:currentColor;display:inline-block;position:relative}
.arrow svg{position:absolute;left:3px;top:3px}

/* header */
.site-header{left:0;top:0;width:1200px;height:94px;background:var(--white)}
.brand{left:112px;top:16px;width:260px;text-align:center;color:var(--blue);font-family:"Figtree",sans-serif;font-weight:600;font-size:40px;line-height:44px}
.brand small{display:block;font-size:18px;letter-spacing:6px;line-height:22px}
.phone-btn{left:590px;top:21px;width:187px;height:46px;background:var(--blue);color:var(--white);font-size:15px;justify-content:center}
.sched-btn{left:800px;top:21px;width:286px;height:46px;border:1px solid #cfd6da;color:var(--ink);font-size:15px;justify-content:center}
.nav{left:0;top:94px;width:1200px;height:49px;background:var(--blue)}
.nav ul{list-style:none;display:flex;position:absolute;left:112px;top:0;height:49px;align-items:center;gap:0}
.nav li{font-family:"Figtree",sans-serif;font-weight:600;font-size:15px;color:var(--white);margin-right:38px;position:relative}
.nav li.active:after{content:"";position:absolute;left:0;right:0;bottom:-10px;height:2px;background:var(--white)}
.hours{left:881px;top:94px;width:251px;height:49px;background:var(--pale);padding:6px 0 0 20px;color:var(--ink)}
.hours b{display:block;font-family:"Figtree",sans-serif;font-size:15px;font-weight:600}
.hours span{font-size:12px}

/* hero */
.hero{left:0;top:143px;width:1200px;height:551px;background:linear-gradient(100deg,#4cc6f4 0%,#7fcbec 40%,#d9e7ef 65%,#8a9fd6 100%)}
.hero-panel{left:109px;top:79px;width:571px;height:292px;background:linear-gradient(90deg,rgba(11,127,192,.95) 0%,rgba(20,150,210,.85) 60%,rgba(40,170,225,0) 100%);padding:26px 0 0 39px}
.hero-panel h1{color:var(--white);font-size:48px;line-height:64px;font-weight:700}
.hero-panel p{color:var(--white);font-size:18px;margin:14px 0 0 4px}
.hero-panel .btn{margin:24px 0 0 0;background:var(--blue-bright);color:var(--white);padding:12px 32px;font-size:18px}

/* procedures */
.procedures{left:0;top:694px;width:1200px;height:779px}
.procedures h2{left:112px;top:84px;font-size:48px;line-height:56px;color:var(--ink);font-weight:700}
.procedures h2 span{color:var(--blue)}
.procedures .intro{left:112px;top:234px;width:440px;font-size:16.5px;line-height:29px}
.card{border-radius:20px;overflow:hidden}
.card .label{position:absolute;left:0;right:0;bottom:26px;text-align:center;color:var(--white);font-family:"Figtree",sans-serif;font-weight:700;font-size:21px}
.card.feature{background:var(--blue-bright);padding:66px 0 0 25px;color:var(--white)}
.card.feature h3{font-size:21px;font-weight:700}
.card.feature p{font-size:15.5px;line-height:26px;margin-top:6px}

/* about */
.about{left:0;top:1473px;width:1200px;height:695px;background:var(--pale)}
.about-photo{left:111px;top:89px;width:477px;height:480px;border-radius:50% 50% 50% 0/50% 50% 50% 0;background:linear-gradient(135deg,#e9f1f6,#c9dbe8 55%,#8eaecb);border:4px solid var(--blue-bright)}
.about-small{left:99px;top:395px;width:186px;height:186px;border-radius:50%;background:linear-gradient(135deg,#f3f7fa,#b9cbd8);border:8px solid var(--blue-bright)}
.about h2{left:655px;top:96px;font-size:46px;line-height:56px;color:var(--ink);font-weight:700}
.about h2 span{color:var(--blue)}
.about .copy{left:654px;top:246px;width:420px;font-size:15px;line-height:30px;color:#333}
.about .btn{left:654px;top:511px;background:var(--blue-bright);color:var(--white);padding:12px 29px;font-size:18px}

/* schedule */
.schedule{left:0;top:2168px;width:1200px;height:524px;background:var(--blue);text-align:center;color:var(--white)}
.schedule h2{position:absolute;left:0;width:1200px;top:102px;font-size:50px;font-weight:700}
.schedule h3{position:absolute;left:0;width:1200px;top:212px;font-size:44px;font-weight:700}
.schedule p{position:absolute;left:250px;width:700px;top:289px;font-size:17px;line-height:30px}
.schedule .btn{position:absolute;left:460px;top:384px;width:280px;height:46px;justify-content:center;border:2px solid var(--white);color:var(--white);font-size:18px}

/* footer */
.site-footer{left:0;top:2692px;width:1200px;height:546px;background:radial-gradient(circle at 50% 40%,#ffffff 55%,#eef2f4 100%)}
.footer-brand{left:400px;top:72px;width:400px;text-align:center;color:var(--ink);font-family:"Figtree",sans-serif;font-weight:600;font-size:60px;line-height:62px}
.footer-brand small{display:block;font-size:26px;letter-spacing:8px;line-height:40px}
.contact{display:flex;gap:32px;top:236px}
.contact .ic{width:68px;height:68px;border-radius:50%;background:var(--blue-bright);display:flex;align-items:center;justify-content:center;flex:none}
.contact b{display:block;font-family:"Arimo",sans-serif;font-size:18px;color:var(--ink);margin-top:4px}
.contact span{font-size:16.5px;line-height:27px;color:#333}
.social{left:476px;top:3px;display:flex;gap:7px;top:397px}
.social i{width:44px;height:44px;border-radius:50%;border:2px solid var(--ink);display:block}
.social i:first-child{border-color:var(--blue-bright)}
.copyright{left:0;width:1200px;top:470px;text-align:center;font-size:16.5px;color:var(--ink)}
</style>
</head>
<body>

<header class="site-header abs">
  <div class="brand abs">Harrowfield<small>DENTISTRY</small></div>
  <a class="btn phone-btn abs" href="#">
    <svg width="26" height="26" viewBox="0 0 24 24" fill="none" stroke="#fff" stroke-width="1.5"><path d="M5 3h4l2 5-3 2a11 11 0 0 0 6 6l2-3 5 2v4a2 2 0 0 1-2 2A18 18 0 0 1 3 5a2 2 0 0 1 2-2z"/></svg>
    (615) 555-0142
  </a>
  <a class="btn sched-btn abs" href="#">
    <svg width="30" height="30" viewBox="0 0 24 24" fill="none" stroke="#0a9ad6" stroke-width="1.4"><rect x="3" y="4" width="16" height="16" rx="2"/><path d="M3 9h16M7 2v4M15 2v4"/><circle cx="18" cy="18" r="4" fill="#fff"/><path d="M16 18l1.5 1.5L20 17"/></svg>
    Schedule Your Appointment
  </a>
</header>

<nav class="nav abs">
  <ul>
    <li class="active">Home</li><li>About</li><li>Services</li><li>Testimonials</li><li>Specials</li><li>Patient Information</li><li>Contact</li>
  </ul>
</nav>
<div class="hours abs"><b>Operating hours</b><span>Monday – Friday: 8:00 AM – 6:00 PM</span></div>

<section class="hero abs" role="img" aria-label="Smiling patient in a dental chair during a check-up">
  <div class="hero-panel abs">
    <h1>Welcome to<br>Harrowfield Dentistry</h1>
    <p>Modern, compassionate dental care for the whole family.</p>
    <a class="btn" href="#">Book Now <span class="arrow" style="color:#fff"><svg width="11" height="11" viewBox="0 0 10 10"><path d="M2 5h6M5 2l3 3-3 3" stroke="#14aee6" stroke-width="1.8" fill="none"/></svg></span></a>
  </div>
</section>

<section class="procedures abs">
  <h2 class="abs">Procedures<br><span>Dental Services</span></h2>
  <p class="intro abs">We offer a full range of dental services using state-of-the-art technology and gentle care. Whether you're here for a routine cleaning or a complete smile makeover, you're in expert hands.</p>

  <div class="card feature abs" style="left:601px;top:101px;width:234px;height:276px">
    <h3>Cosmetic Dentistry</h3>
    <p>Brighten, straighten,<br>and perfect your smile.</p>
  </div>
  <div class="card abs" role="img" aria-label="Model of teeth with a dental implant" style="left:853px;top:101px;width:234px;height:276px;background:linear-gradient(180deg,#ece6e0,#b98a80 60%,#6f2f2c)"><span class="label">Implants</span></div>
  <div class="card abs" role="img" aria-label="Close-up of clean white teeth" style="left:111px;top:399px;width:234px;height:276px;background:linear-gradient(180deg,#b7726a,#e7e1de 45%,#6a3b38)"><span class="label">Dental Hygiene</span></div>
  <div class="card abs" role="img" aria-label="Person holding their jaw in tooth pain" style="left:358px;top:399px;width:234px;height:276px;background:linear-gradient(180deg,#8c7f77,#b98a7c 50%,#4d3f3b)"><span class="label">Emergency Services</span></div>
  <div class="card abs" role="img" aria-label="Smiling patient after a restoration" style="left:606px;top:399px;width:234px;height:276px;background:linear-gradient(180deg,#c8d6d8,#b39b8a 50%,#4f5a60)"><span class="label">Restorations</span></div>
  <div class="card abs" role="img" aria-label="Patient fitting a denture" style="left:853px;top:399px;width:234px;height:276px;background:linear-gradient(180deg,#d8c3b5,#c59683 50%,#52606a)"><span class="label">Dentures</span></div>
</section>

<section class="about abs">
  <div class="about-photo abs" role="img" aria-label="Two smiling dental team members"></div>
  <div class="about-small abs" role="img" aria-label="Modern dental treatment room"></div>
  <h2 class="abs">About <span>Harrowfield</span><br>Dentistry</h2>
  <div class="copy abs">
    <p>At Harrowfield Dentistry, we believe a healthy smile begins with trust and comfort. Our modern dental office is designed with your experience in mind — combining advanced technology, skilled care, and a calming environment to help you feel right at home.</p>
    <p style="margin-top:30px">Whether you're here for a routine cleaning or a complete smile makeover, you're in expert hands.</p>
  </div>
  <a class="btn abs" href="#">Read More <span class="arrow" style="color:#fff"><svg width="11" height="11" viewBox="0 0 10 10"><path d="M2 5h6M5 2l3 3-3 3" stroke="#14aee6" stroke-width="1.8" fill="none"/></svg></span></a>
</section>

<section class="schedule abs">
  <h2>Schedule an Appointment</h2>
  <h3>Book Your Visit Today</h3>
  <p>Use our easy online scheduler to reserve a time that works for you — or call us directly to speak with a team member.</p>
  <a class="btn" href="#">Schedule Appointment <span class="arrow" style="color:#fff"><svg width="11" height="11" viewBox="0 0 10 10"><path d="M2 5h6M5 2l3 3-3 3" stroke="#0a9ad6" stroke-width="1.8" fill="none"/></svg></span></a>
</section>

<footer class="site-footer abs">
  <div class="footer-brand abs">Harrowfield<small>DENTISTRY</small></div>
  <div class="contact abs" style="left:113px">
    <div class="ic"><svg width="22" height="28" viewBox="0 0 20 26"><path d="M10 1a8 8 0 0 0-8 8c0 6 8 16 8 16s8-10 8-16a8 8 0 0 0-8-8z" fill="#fff"/><circle cx="10" cy="9" r="3" fill="#14aee6"/></svg></div>
    <div><b>Address:</b><span>48 Alder Court, Suite<br>100, YourTown, ST 12345</span></div>
  </div>
  <div class="contact abs" style="left:484px">
    <div class="ic"><svg width="26" height="26" viewBox="0 0 24 24"><path d="M5 3h4l2 5-3 2a11 11 0 0 0 6 6l2-3 5 2v4a2 2 0 0 1-2 2A18 18 0 0 1 3 5a2 2 0 0 1 2-2z" fill="#fff"/></svg></div>
    <div><b>Call Us:</b><span>(615) 555-0142</span></div>
  </div>
  <div class="contact abs" style="left:760px">
    <div class="ic"><svg width="30" height="22" viewBox="0 0 30 22"><rect x="1" y="1" width="28" height="20" rx="2" fill="#fff"/><path d="M2 3l13 10L28 3" stroke="#14aee6" stroke-width="2" fill="none"/></svg></div>
    <div><b>Email:</b><span>hello@harrowfielddentistry.com</span></div>
  </div>
  <div class="social abs" aria-label="Social media links"><i></i><i></i><i></i><i></i><i></i></div>
  <p class="copyright abs">© Copyright 2025 Harrowfield Dentistry. All Rights Reserved</p>
</footer>

</body>
</html>
```